We need UI/UX design for a public, informational website for The Copper Lantern.
The pages, structure, and content scope are already defined. Designers are required to work only on the UI/UX layout of these existing pages, focusing on clarity, hierarchy, spacing, and usability. Do not add, remove, rename, or reinterpret pages or content.
The website is strictly informational only. It must not include accounts, onboarding, payments, custody, escrow administration, marketplaces, dashboards, or any transactional functionality.
Scope of work
Apply UI/UX design to the predefined website pages
Design layout for text, images, notices, and sections
Ensure consistent components and layout patterns across page types
Optimize layouts for long form, compliance focused content
Content writing, page creation, and branding changes are out of scope.
Structure reference
The complete page list, hierarchy, and content definitions are provided in the technical documentation and must be treated as the primary source of truth.
A Figma link is provided only as a light visual reference for page existence and structure:
https://meadow-knot-48203956.plumsite.example/
Designers must rely on the documentation for in depth and authoritative reference.
Brand guidelines
The Copper Lantern has existing brand guidelines and official logos, including light and dark versions. These assets will be provided and must be followed exactly. Designers must not redesign, alter, or reinterpret the brand identity.
Look and feel direction
The desired visual direction is inspired by:
https://ledgerwaltz.example/
This reference is provided only to indicate:
Institutional and enterprise tone
Clean, modern typography
Strong hierarchy and generous whitespace
Editorial, content first layouts
Do not copy branding, layouts, components, or assets from the reference site.
Hero section direction
The hero section should follow a similar structural approach to the hero used on https://ledgerwaltz.example/
, meaning:
Strong editorial framing
Clear headline hierarchy
Calm, institutional first impression
However, the background video must be Abu Dhabi focused, not generic or global. The video should visually reflect:
Abu Dhabi skyline or architectural language
Institutional, sovereign, long term infrastructure tone
Clean, slow, cinematic motion
No promotional, marketing, or lifestyle visuals
The hero must remain informational, restrained, and credible. No hype. No calls to invest. No implied participation.
Constraints
One global primary CTA only: “Continue to Halvemark” (external)
All other interactions must be informational
No visuals or language implying offers, investment, eligibility, or participation
Clear separation between informational content and any external operational platforms
Deliverables
High fidelity UI/UX designs created in Figma, covering:
Desktop layouts
Tablet layouts where relevant
Mobile layouts
Complete Figma file(s) including:
All designed pages defined in the technical documentation
A reusable component library (headers, footers, cards, notice panels, forms, CTAs, typography styles, spacing system)
Clearly defined layout grids, spacing rules, and text styles
Proper use of components and variants, not detached frames
Designs prepared for developer handoff, including:
Clear layer naming and structure
Auto layout where appropriate
Consistent use of styles and components
Responsive behavior demonstrated within Figma
Notes or annotations only where necessary for clarity
No prototypes, interactions, or motion design beyond basic layout states, unless explicitly requested. The focus is static UI/UX clarity, not animation.
A detailed technical specification document and official brand assets will be provided.
Any designs delivered outside Figma, that alter structure or content, or that ignore the defined constraints, boundaries, or tone will be rejected.

```html
<!DOCTYPE html>
<html lang="en">
<head>
<meta charset="utf-8">
<title>The Copper Lantern</title>
<link href="https://fonts.googleapis.com/css2?family=Archivo:wght@300;400;800;900&family=Inter:wght@400;500;600&display=swap" rel="stylesheet">
<style>
:root{
  --ink:#0b1526;
  --text:#5a5f66;
  --white:#ffffff;
  --band-blue:#f2f6fd;
  --band-grey:#f2f2f2;
  --footer:#0b1526;
}
*{box-sizing:border-box;margin:0;padding:0}
html,body{width:1200px;height:4054px;overflow:hidden}
body{position:relative;background:var(--white);font-family:"Inter",sans-serif;color:var(--ink)}
.abs{position:absolute}
.heading{font-family:"Archivo",sans-serif;font-weight:300;font-size:35px;line-height:48px;letter-spacing:-0.8px;color:var(--ink)}
.heading b{font-weight:900}
.copy{font-size:13.5px;line-height:24px;color:var(--text);text-align:justify}
.btn{display:flex;align-items:center;justify-content:center;gap:8px;border-radius:30px;font-size:14.5px;font-weight:600;white-space:nowrap}
.btn-outline{border:1.5px solid var(--ink);color:var(--ink);background:var(--white)}
.btn-dark{background:var(--ink);color:var(--white)}
.btn-light{background:var(--white);color:var(--ink)}
.arrow{width:14px;height:14px}
.photo{position:absolute}

/* hero */
.hero{position:absolute;left:0;top:0;width:1200px;height:685px;background:linear-gradient(180deg,#6f8aa6 0%,#a9b6c1 18%,#8c8c80 34%,#6c6a5c 44%,#d9cfb9 49%,#3f8a9a 55%,#1f5d72 75%,#173f55 100%)}
.nav{position:absolute;top:28px;left:0;width:1200px;height:50px}
.brand{position:absolute;display:flex;align-items:center;gap:8px;font-family:"Inter",sans-serif;font-weight:500;white-space:nowrap}
.brand .ring{border:2px solid currentColor;border-radius:50%;flex-shrink:0}
.nav-links{position:absolute;left:311px;top:0;height:22px;display:flex;gap:24px;font-size:14.5px;color:var(--white)}
.nav-links .active{text-decoration:underline;text-underline-offset:6px}
.hero-title{position:absolute;right:646px;top:498px;text-align:right;color:var(--white);font-family:"Archivo",sans-serif;letter-spacing:-1px;white-space:nowrap}
.hero-title .l1{font-weight:400;font-size:50px;line-height:62px}
.hero-title .l2{font-weight:900;font-size:48px;line-height:66px}
.hero-copy{position:absolute;left:605px;top:482px;width:455px;color:var(--white);font-size:16px;line-height:27px}

/* ecosystem */
.eco{position:absolute;left:0;top:1800px;width:1200px;height:474px;background:var(--band-blue);text-align:center}
.eco .col h3{font-weight:400;font-size:17.5px;color:var(--ink);margin-bottom:12px}
.eco .col p{font-size:13.5px;line-height:24px;color:var(--text)}

/* contact band */
.contact{position:absolute;left:0;top:3394px;width:1200px;height:304px;background:var(--band-grey);text-align:center}

/* footer */
.footer{position:absolute;left:0;top:3698px;width:1200px;height:356px;background:var(--footer);color:var(--white)}
.footer h4{font-weight:500;font-size:15px;letter-spacing:0.3px;margin-bottom:12px}
.footer ul{list-style:none;font-size:13.5px;line-height:24px}
.social{position:absolute;top:3872px;display:flex;gap:10px;left:172px}
.social span{width:27px;height:27px;border:1.5px solid var(--white);border-radius:50%;display:block}
.contact-row{display:flex;align-items:flex-start;gap:12px;font-size:13.5px;line-height:21px;margin-bottom:17px}
.contact-row .ico{width:24px;height:24px;border-radius:50%;background:var(--white);display:flex;align-items:center;justify-content:center;flex-shrink:0}
</style>
</head>
<body>

<header class="hero" role="img" aria-label="Aerial view of the Abu Dhabi skyline, beach and coastal water"></header>
<nav class="nav">
  <div class="brand" style="left:104px;top:-8px;color:var(--white);font-size:12.5px">
    <span class="ring" style="width:46px;height:46px"></span>The Copper Lantern
  </div>
  <div class="nav-links">
    <span class="active">Home</span><span>Framework</span><span>Projects</span><span>Halvemark</span><span>Insights</span><span>Company</span><span>Contact</span>
  </div>
  <div class="btn" style="position:absolute;left:888px;top:-9px;width:210px;height:44px;border:1.5px solid var(--white);color:var(--white)">Continue to Halvemark</div>
</nav>
<h1 class="hero-title"><div class="l1">Welcome To</div><div class="l2">The Copper Lantern</div></h1>
<p class="hero-copy">Its purpose is to define structural standards and oversight principles for complex initiatives that may involve multiple parties, staged execution, &amp; longterm accountability.</p>
<div class="btn btn-light abs" style="left:606px;top:592px;width:256px;height:47px">Learn the Framework
  <svg class="arrow" viewBox="0 0 16 16"><circle cx="8" cy="8" r="8" fill="#0b1526"/><path d="M6.5 4.5 10 8l-3.5 3.5" stroke="#fff" stroke-width="2" fill="none"/></svg></div>

<section>
  <h2 class="heading abs" style="left:143px;top:790px;width:420px">Governance <b>and Project Origination</b></h2>
  <p class="copy abs" style="left:143px;top:912px;width:412px">Governance in this context refers to the standards that determine how projects are structured and how oversight is described. Origination refers to the initial design and definition of an initiative, including role separation, reporting expectations, and boundary setting before execution begins. The Copper Lantern focuses on these governance-level elements rather than on operating day-to-day workflows.</p>
  <div class="btn btn-outline abs" style="left:143px;top:1120px;width:159px;height:44px">Learn More
    <svg class="arrow" viewBox="0 0 16 16"><circle cx="8" cy="8" r="8" fill="#0b1526"/><path d="M6.5 4.5 10 8l-3.5 3.5" stroke="#fff" stroke-width="2" fill="none"/></svg></div>
  <div class="photo" role="img" aria-label="Aerial view of an island resort and causeway in turquoise water" style="left:598px;top:762px;width:602px;height:441px;background:linear-gradient(160deg,#7fb9cf 0%,#2f9ab0 40%,#d8d3c2 65%,#5e8a5b 85%,#c9c9c9 100%)"></div>
</section>

<section>
  <div class="photo" role="img" aria-label="Dense city skyline of towers seen from above" style="left:0;top:1282px;width:600px;height:440px;background:linear-gradient(180deg,#9fb5cc 0%,#7e8c98 35%,#5b6670 70%,#8a8374 100%)"></div>
  <h2 class="heading abs" style="left:643px;top:1308px"><b>Clear Role</b> Separation</h2>
  <p class="copy abs" style="left:643px;top:1383px;width:412px">The ecosystem is designed around clear separation of responsibilities. Governance activities belong at the framework layer. Operational workflows, where available, belong on a separate operating platform designed for process execution and recordkeeping. Assets and project execution, where applicable, belong at the project level through ring-fenced structures created for specific initiatives. This separation is intended to reduce ambiguity and help stakeholders understand who is responsible for what.</p>
  <div class="btn btn-outline abs" style="left:643px;top:1640px;width:160px;height:44px">Learn More
    <svg class="arrow" viewBox="0 0 16 16"><circle cx="8" cy="8" r="8" fill="#0b1526"/><path d="M6.5 4.5 10 8l-3.5 3.5" stroke="#fff" stroke-width="2" fill="none"/></svg></div>
</section>

<section class="eco">
  <h2 class="heading" style="margin-top:47px">How <b>the Ecosystem</b> Works</h2>
  <p style="font-size:17px;margin-top:6px;color:var(--ink)">At a high level, the ecosystem can be understood as three layers:</p>
  <p style="font-size:13.5px;line-height:24px;color:var(--text);width:860px;margin:12px auto 0">This website focuses on the governance layer and provides links to learn about structural concepts such as role separation, escrow and milestone framing, and recordkeeping terminology.</p>
  <div class="col abs" style="left:140px;top:222px;width:290px"><h3>Governance</h3><p>Defines standards, explains role boundaries, and publishes framework information</p></div>
  <div class="col abs" style="left:462px;top:222px;width:286px"><h3>Operations</h3><p>Manages workflow processes such as documentation steps and record-anchored auditevents through a separate platform.</p></div>
  <div class="col abs" style="left:780px;top:222px;width:282px"><h3>Project Execution</h3><p>Occurs at the project level through dedicated structures that hold responsibilities &amp; assets where applicable.</p></div>
  <div class="btn btn-dark abs" style="left:488px;top:364px;width:224px;height:43px">Continue to Halvemark
    <svg class="arrow" viewBox="0 0 16 16"><circle cx="8" cy="8" r="8" fill="#fff"/><path d="M6.5 4.5 10 8l-3.5 3.5" stroke="#0b1526" stroke-width="2" fill="none"/></svg></div>
</section>

<section>
  <h2 class="heading abs" style="left:143px;top:2383px;width:440px">Independent <b>Escrow and Milestone</b> Oversight</h2>
  <p class="copy abs" style="left:143px;top:2505px;width:412px">Some initiatives use independent escrow arrangements to coordinate staged releases linked to milestone completion. Escrow can support execution discipline by requiring defined evidence before releases occur.Escrow does not guarantee outcomes, timelines, or success, and it is not administered by this website operator. This site describes the concept for clarity and transparency.</p>
  <div class="btn btn-outline abs" style="left:143px;top:2712px;width:159px;height:44px">Learn More
    <svg class="arrow" viewBox="0 0 16 16"><circle cx="8" cy="8" r="8" fill="#0b1526"/><path d="M6.5 4.5 10 8l-3.5 3.5" stroke="#fff" stroke-width="2" fill="none"/></svg></div>
  <div class="photo" role="img" aria-label="Aerial view of curved glass towers and a tall slim tower by the coast" style="left:598px;top:2355px;width:602px;height:441px;background:linear-gradient(150deg,#a8c4d8 0%,#6d8294 35%,#8d9a7a 60%,#c2bfb2 80%,#dedbd6 100%)"></div>
</section>

<section>
  <div class="photo" role="img" aria-label="Waterfront promenade with palm trees and city towers under a clear sky" style="left:0;top:2873px;width:600px;height:441px;background:linear-gradient(180deg,#9cc5e6 0%,#c7dced 40%,#4a6b8a 62%,#4f7d58 72%,#2ea7b7 85%,#188fa0 100%)"></div>
  <h2 class="heading abs" style="left:643px;top:2929px;width:420px">Where <b>Operational</b> Workflows <b>Happen</b></h2>
  <p class="copy abs" style="left:643px;top:3044px;width:412px">Operational workflows, including any onboarding or workflow participation where permitted, occur on a separate operating platform under separate terms &amp; policies. If you need operational access, use the Halvemark page on this site to navigate externally. This website does not host those workflows.</p>
  <div class="btn btn-outline abs" style="left:643px;top:3203px;width:160px;height:44px">Learn More
    <svg class="arrow" viewBox="0 0 16 16"><circle cx="8" cy="8" r="8" fill="#0b1526"/><path d="M6.5 4.5 10 8l-3.5 3.5" stroke="#fff" stroke-width="2" fill="none"/></svg></div>
</section>

<section class="contact">
  <h2 class="heading" style="margin-top:50px">Contact <b>and Inquiries</b></h2>
  <p style="font-size:15px;line-height:27px;color:var(--text);width:900px;margin:8px auto 0">If you have questions about governance framework concepts, role boundaries, or information published on this website, you can contact the team using the Contact page. Do not submit sensitive personal data through public forms</p>
  <div class="btn btn-outline abs" style="left:501px;top:197px;width:198px;height:44px">Contact the Team
    <svg class="arrow" viewBox="0 0 16 16"><circle cx="8" cy="8" r="8" fill="#0b1526"/><path d="M6.5 4.5 10 8l-3.5 3.5" stroke="#fff" stroke-width="2" fill="none"/></svg></div>
</section>

<footer class="footer">
  <div class="brand" style="left:143px;top:67px;color:var(--white);font-size:16px">
    <span class="ring" style="width:64px;height:64px"></span>The Copper Lantern
  </div>
  <div class="abs" style="left:417px;top:66px"><h4>NAVIGATION</h4>
    <ul><li>Framework</li><li>Projects</li><li>Halvemark</li><li>Insights</li><li>Company</li><li>Contact</li></ul></div>
  <div class="abs" style="left:591px;top:66px"><h4>OTHER LINKS</h4>
    <ul><li>Legal</li><li>Terms of Use</li><li>Privacy Policy</li><li>Cookie Policy</li><li>Disclaimer &amp; Risk Notices</li><li>Acceptable Use Policy</li><li>Accessibility Statement</li><li>Glossary</li></ul></div>
  <div class="abs" style="left:832px;top:66px;width:260px"><h4>CONTACT US</h4>
    <div class="contact-row"><span class="ico"><svg width="12" height="12" viewBox="0 0 24 24"><path d="M6.6 10.8a15 15 0 0 0 6.6 6.6l2.2-2.2a1 1 0 0 1 1-.25 11 11 0 0 0 3.6.6 1 1 0 0 1 1 1V20a1 1 0 0 1-1 1A17 17 0 0 1 3 4a1 1 0 0 1 1-1h3.5a1 1 0 0 1 1 1 11 11 0 0 0 .6 3.6 1 1 0 0 1-.25 1z" fill="#0b1526"/></svg></span><span style="padding-top:2px">+1-555-010-0199</span></div>
    <div class="contact-row"><span class="ico"><svg width="12" height="12" viewBox="0 0 24 24"><rect x="2" y="5" width="20" height="14" rx="2" fill="#0b1526"/><path d="M3 6l9 7 9-7" stroke="#fff" stroke-width="1.8" fill="none"/></svg></span><span style="padding-top:2px">info@copperlantern.example</span></div>
    <div class="contact-row"><span class="ico"><svg width="12" height="12" viewBox="0 0 24 24"><path d="M12 2a7 7 0 0 0-7 7c0 5 7 13 7 13s7-8 7-13a7 7 0 0 0-7-7z" fill="#0b1526"/><circle cx="12" cy="9" r="2.5" fill="#fff"/></svg></span><span>214 Quayside Lane, Suite 5, Marlow Bay 40218</span></div>
  </div>
  <div class="abs" style="left:0;top:323px;width:1200px;text-align:center;font-size:13.5px">2026&nbsp; Copyright - The Copper Lantern | All Rights Reserved</div>
</footer>
<div class="social"><span></span><span></span><span></span><span></span></div>

</body>
</html>
```